Social Media App Needs PPT Template

We need a PowerPoint template for a new social media company based in the DC area called "Bold Ledger." We provide an interactive digital platform for executives to share actionable advice. We would like to see designs that use our orange logo color as an accent, but are mainly grey, white, and black. The final design should communicate clean, chic, modern, and professional.

Target Market(s)

Executives

Industry/Entity Type

Information Technology

Font styles to use
Sans Serif

Colors
f78f20
fbe7d2
ffffff
000000
e8e8e8
757575

Requirements
Must have
• My project must have title page and many options for the body of the ppt (graphs, tables, etc). It also needs to be easy to modify. I must have someone who is experienced in creating powerpoint templates.
Nice to have
• It would be nice to have a very modern and clean design that includes the logo on every page, but still leaves a lot of room for the content of the slide
Should not have
• My design project should not look to busy.

```html
<!DOCTYPE html>
<html lang="en">
<head>
<meta charset="utf-8">
<title>Bold Ledger – Slide Template</title>
<link href="https://fonts.googleapis.com/css2?family=Lato:wght@300;400;700&display=swap" rel="stylesheet">
<style>
  :root {
    --board-bg: #cbcbcb;
    --white: #ffffff;
    --orange: #f39320;
    --navy: #222d3b;
    --grey: #6d6d6d;
    --ink: #231f20;
    --muted: #6b6b6b;
    --rule: #555a70;
    --side-text: #dcdfe4;
  }
  * { box-sizing: border-box; margin: 0; padding: 0; }
  html, body {
    width: 1200px; height: 960px; overflow: hidden;
    background: var(--board-bg);
    font-family: "Lato", Arial, sans-serif;
  }
  .board-label {
    position: absolute; top: 64px; left: 0; width: 1200px;
    text-align: center; color: var(--white);
    font-weight: 300; font-size: 32px; letter-spacing: 0.5px;
  }
  .slide {
    position: absolute; left: 120px; top: 143px;
    width: 958px; height: 719px; background: var(--white);
  }
  .sidebar {
    position: absolute; left: 0; top: 0; width: 170px; height: 100%;
    background: var(--navy);
  }
  .brand {
    position: absolute; top: 212px; left: 0; width: 170px;
    display: flex; align-items: center; justify-content: center; gap: 8px;
    color: var(--white); font-weight: 700; font-size: 19px;
  }
  .brand-dot { width: 12px; height: 12px; border-radius: 50%; background: var(--orange); }
  .brand { top: 70px; }
  .site-url {
    position: absolute; left: 19px; top: 667px;
    color: var(--side-text); font-size: 18px; font-weight: 400;
  }
  .page-title {
    position: absolute; left: 205px; top: 96px;
    color: var(--orange); font-weight: 400; font-size: 40px;
  }
  .title-rule {
    position: absolute; left: 205px; top: 155px; width: 716px; height: 1px;
    background: var(--orange);
  }
  .stat {
    position: absolute; width: 336px; height: 150px; color: var(--white);
  }
  .stat--orange { left: 199px; top: 215px; background: var(--orange); }
  .stat--grey { left: 575px; top: 215px; background: var(--grey); }
  .stat--navy { left: 199px; top: 402px; background: var(--navy); }
  .stat--black { left: 575px; top: 402px; background: var(--ink); }
  .stat-icon {
    position: absolute; left: 18px; top: 43px; width: 70px; height: 64px;
    display: flex; align-items: center; justify-content: center;
  }
  .stat-value {
    position: absolute; left: 112px; top: 20px;
    font-size: 29px; font-weight: 400; line-height: 1;
  }
  .stat-text {
    position: absolute; left: 112px; top: 60px; width: 200px;
    font-size: 13.5px; line-height: 17px; font-weight: 400;
  }
  .icon-placeholder {
    width: 58px; height: 44px; border-radius: 20px; background: #e9ecef;
  }
  .footer-rule {
    position: absolute; left: 802px; top: 664px; width: 124px; height: 1px;
    background: var(--rule);
  }
  .page-number {
    position: absolute; right: 36px; top: 689px;
    color: var(--muted); font-size: 13px;
  }
</style>
</head>
<body>
  <div class="board-label">Page 9</div>

  <main class="slide">
    <aside class="sidebar">
      <div class="brand"><span class="brand-dot"></span>Bold Ledger</div>
      <div class="site-url">boldledger.com</div>
    </aside>

    <h1 class="page-title">Title of the page</h1>
    <div class="title-rule"></div>

    <section class="stat stat--orange">
      <div class="stat-icon">
        <svg width="68" height="48" viewBox="0 0 68 48" fill="none" stroke="#fff" stroke-width="3.5" stroke-linejoin="round" stroke-linecap="round">
          <rect x="3" y="16" width="8" height="14"/>
          <path d="M11 16 L48 4 V42 L11 30 Z"/>
          <path d="M18 32 L20 42 H30 L28 35"/>
          <rect x="48" y="2" width="6" height="42" rx="2"/>
          <path d="M59 15 L65 12 M59 23 H66 M59 31 L65 34"/>
        </svg>
      </div>
      <div class="stat-value">915,456,459</div>
      <p class="stat-text">Lorem ipsum dolor sit amet, consectetuer adipiscing elit, s ed diam nonu mmy nibh euis mod tincidunt</p>
    </section>

    <section class="stat stat--grey">
      <div class="stat-icon">
        <svg width="58" height="68" viewBox="0 0 58 68" fill="none" stroke="#fff" stroke-width="3.5" stroke-linejoin="round">
          <path d="M18 4 H40 L34 16 H24 Z"/>
          <path d="M22 18 H36"/>
          <path d="M24 20 C8 28 2 42 4 54 C6 64 14 66 29 66 C44 66 52 64 54 54 C56 42 50 28 34 20 Z"/>
          <text x="29" y="52" text-anchor="middle" fill="#fff" stroke="none" font-family="Lato, Arial, sans-serif" font-weight="700" font-size="24">$</text>
        </svg>
      </div>
      <div class="stat-value">111,458,564</div>
      <p class="stat-text">Lorem ipsum dolor sit amet, consectetuer adipiscing elit, s ed diam nonu mmy nibh euis mod tincidunt</p>
    </section>

    <section class="stat stat--navy">
      <div class="stat-icon">
        <div class="icon-placeholder" role="img" aria-label="Savings icon with coin"></div>
      </div>
      <div class="stat-value">100%</div>
      <p class="stat-text">Lorem ipsum dolor sit amet, consectetuer adipiscing elit, s ed diam nonu mmy nibh euis mod tincidunt</p>
    </section>

    <section class="stat stat--black">
      <div class="stat-icon">
        <svg width="56" height="52" viewBox="0 0 56 52" fill="none" stroke="#fff" stroke-width="3.5" stroke-linejoin="round">
          <rect x="3" y="36" width="12" height="14"/>
          <rect x="15" y="24" width="12" height="26"/>
          <rect x="27" y="12" width="12" height="38"/>
          <rect x="39" y="2" width="12" height="48"/>
        </svg>
      </div>
      <div class="stat-value">100%</div>
      <p class="stat-text">Lorem ipsum dolor sit amet, consectetuer adipiscing elit, s ed diam nonu mmy nibh euis mod tincidunt</p>
    </section>

    <div class="footer-rule"></div>
    <div class="page-number">Page 8</div>
  </main>
</body>
</html>
```